Business Card Design for Training Business

Clear Path Coaching is a new business that delivers training and other services with a focus on topics related to mental health and wellbeing, for example, Wellmind Response Course, Resilience etc. We have a strong focus on evidence-based psychology and neuroscience. I have a logo which I will upload with the brief, so please consider colours that work well with the logo.
Target Market(s)
Adults, workplaces (particularly government and not-for-profits)
Industry/Entity Type
Business
Contact Information for Business Card
Head Strong TrainingSamantha SellwoodDirector0438 770 850sam@headstrongtraining.com.auwww.headstrongtraining.com.au

```html
<!DOCTYPE html>
<html lang="en">
<head>
<meta charset="utf-8">
<title>Clear Path Coaching – Business Card</title>
<link href="https://fonts.googleapis.com/css2?family=Arimo:wght@400;700&display=swap" rel="stylesheet">
<style>
  :root {
    --stage: #ece9e4;
    --card: #ffffff;
    --band-light: #f1f1f2;
    --band-mid: #e4e4e6;
    --mark: #3fb7c2;
    --brand-grey: #8a8a8c;
    --ink: #111111;
    --ink-soft: #222222;
  }
  * { margin: 0; padding: 0; box-sizing: border-box; }
  html, body {
    width: 1200px;
    height: 902px;
    overflow: hidden;
    background: var(--stage);
    font-family: "Arimo", Arial, sans-serif;
  }
  .stage {
    position: relative;
    width: 1200px;
    height: 902px;
  }
  .card {
    position: absolute;
    left: 170px;
    top: 188px;
    width: 860px;
    height: 526px;
    background: var(--card);
    box-shadow: 0 10px 30px rgba(0,0,0,0.12);
    overflow: hidden;
  }
  .card__band {
    position: absolute;
    left: 0;
    top: 232px;
    width: 100%;
    height: 226px;
    background: linear-gradient(90deg, var(--band-light) 0%, var(--band-mid) 45%, var(--band-light) 100%);
  }
  .brand {
    position: absolute;
    top: 34px;
    left: 0;
    width: 100%;
    text-align: center;
    color: var(--brand-grey);
    font-weight: 400;
  }
  .brand__dot {
    display: block;
    width: 92px;
    height: 92px;
    margin: 0 auto 14px;
    border: 2px solid var(--mark);
    border-radius: 50%;
  }
  .brand__name {
    font-size: 34px;
    line-height: 38px;
    letter-spacing: 4px;
    text-transform: uppercase;
  }
  .brand__sub {
    font-size: 15px;
    line-height: 20px;
    letter-spacing: 9px;
    text-transform: uppercase;
    margin-top: 4px;
    padding-left: 9px;
  }
  .contact {
    position: absolute;
    top: 254px;
    left: 0;
    width: 100%;
    text-align: center;
    color: var(--ink);
  }
  .contact__name {
    font-weight: 700;
    font-size: 27px;
    line-height: 32px;
  }
  .contact__role {
    font-weight: 700;
    font-size: 16px;
    line-height: 20px;
    margin-top: 2px;
  }
  .contact__list {
    list-style: none;
    margin-top: 20px;
    font-size: 21px;
    line-height: 38px;
    color: var(--ink-soft);
  }
</style>
</head>
<body>
<main class="stage">
  <section class="card" aria-label="Business card front">
    <div class="card__band" role="img" aria-label="Soft grey band with a faint pattern of interlocking gears inside a head silhouette"></div>
    <header class="brand">
      <span class="brand__dot"></span>
      <p class="brand__name">Clear Path</p>
      <p class="brand__sub">Coaching</p>
    </header>
    <div class="contact">
      <p class="contact__name">Rebecca Tanfield</p>
      <p class="contact__role">Director</p>
      <ul class="contact__list">
        <li>0491 362 517</li>
        <li>bec@clearpathcoaching.example.au</li>
        <li>www.clearpathcoaching.example.au</li>
      </ul>
    </div>
  </section>
</main>
</body>
</html>
```